Professional and creative business card design for recruiting service providers

Our company supports German medium-sized companies in filling vacancies promptly. For this we use social media marketing and bring our customers into the visibility.

We want a professional but also creative design for our business cards.

Please look at lindqvar-staff.de to get an impression of our CI.

Target Market(s)

Small and medium-sized companies in Germany from the industry

Industry/Entity Type

Industrie, Handwerk

Contact Information for Business Card

Name, Position, Telefonnummer, Email, Website

Colors
EE7325
F08F49
F5BC92
FAE3D3
FDF4ED

Requirements
Must have
• A picture of the employee and in the style of www.lindqvar-staff.de

```html
<!DOCTYPE html>
<html lang="de">
<head>
<meta charset="utf-8">
<title>Lindqvar Staff – Visitenkarte</title>
<link href="https://fonts.googleapis.com/css2?family=Poppins:wght@400;500;700&display=swap" rel="stylesheet">
<style>
  :root {
    --orange: #EE7325;
    --orange-mid: #F08F49;
    --peach: #F5BC92;
    --cream: #FAE3D3;
    --ivory: #FDF4ED;
    --ink: #141414;
    --page: #ffffff;
    --photo-bg: #f4f4f4;
  }
  * { margin: 0; padding: 0; box-sizing: border-box; }
  html, body {
    width: 1200px; height: 1121px; overflow: hidden;
    background: var(--page);
    font-family: "Poppins", sans-serif;
    color: var(--ink);
  }
  .sheet { position: relative; width: 1200px; height: 1121px; }
  .card {
    position: absolute; top: 400px;
    width: 560px; height: 320px; overflow: hidden;
    box-shadow: 10px 12px 14px rgba(0,0,0,0.35);
  }
  /* front */
  .card-front {
    left: 30px;
    background:
      radial-gradient(ellipse 150px 135px at 120px 165px, rgba(240,143,73,0.75), rgba(245,188,146,0.5) 55%, rgba(250,227,211,0) 100%),
      radial-gradient(ellipse 200px 170px at 390px 90px, var(--ivory), rgba(253,244,237,0) 100%),
      radial-gradient(ellipse 120px 80px at 560px 320px, rgba(245,188,146,0.8), rgba(245,188,146,0) 100%),
      var(--cream);
  }
  .brand-lockup {
    position: absolute; left: 278px; top: 205px;
    display: flex; align-items: center; gap: 16px;
  }
  .brand-square { width: 62px; height: 62px; background: var(--orange); }
  .brand-name {
    font-weight: 700; font-size: 29px; line-height: 1.02;
    color: var(--ink); text-transform: uppercase;
  }
  /* back */
  .card-back { left: 610px; background: var(--orange); }
  .back-brand {
    position: absolute; right: 14px; top: 26px;
    display: flex; align-items: center; gap: 6px;
  }
  .back-brand-square { width: 18px; height: 18px; background: var(--ink); }
  .back-brand-name {
    font-weight: 700; font-size: 9.5px; line-height: 1.05;
    text-transform: uppercase; color: var(--ink);
  }
  .portrait {
    position: absolute; left: 31px; top: 73px;
    width: 254px; height: 150px; border-radius: 50%;
    background: linear-gradient(170deg, var(--photo-bg) 0%, #d9d9d9 55%, #3a3a3c 100%);
  }
  .person-name {
    position: absolute; left: 50px; top: 234px;
    font-size: 31px; line-height: 1; font-weight: 400; color: var(--ink);
    text-transform: uppercase; letter-spacing: 0.2px;
  }
  .person-name strong { font-weight: 700; }
  .person-role {
    position: absolute; left: 50px; top: 273px;
    font-size: 13.5px; font-weight: 400; color: var(--ink);
  }
  .contact-list {
    position: absolute; left: 358px; top: 168px;
    list-style: none; font-size: 11.2px; line-height: 14px;
  }
  .contact-item { display: flex; align-items: flex-start; gap: 10px; margin-bottom: 12px; }
  .contact-item:last-child { margin-bottom: 0; }
  .contact-icon { width: 16px; height: 16px; flex: none; }
  .contact-item.address { margin-bottom: 6px; }
</style>
</head>
<body>
<main class="sheet">
  <section class="card card-front" aria-label="Visitenkarte Vorderseite">
    <div class="brand-lockup">
      <span class="brand-square"></span>
      <p class="brand-name">Lindqvar<br>Staff</p>
    </div>
  </section>

  <section class="card card-back" aria-label="Visitenkarte Rückseite">
    <div class="back-brand">
      <span class="back-brand-square"></span>
      <p class="back-brand-name">Lindqvar<br>Staff</p>
    </div>

    <div class="portrait" role="img" aria-label="Porträtfoto des Mitarbeiters im Anzug auf einem Bürostuhl"></div>

    <h1 class="person-name">Jonas <strong>Elbrecht</strong></h1>
    <p class="person-role">Senior Recruiting Berater</p>

    <ul class="contact-list">
      <li class="contact-item">
        <svg class="contact-icon" viewBox="0 0 16 16"><circle cx="8" cy="8" r="8" fill="var(--ink)"/><path d="M5.2 4.2l1.5-.2.7 1.8-.9.7c.5 1.1 1.3 1.9 2.4 2.4l.7-.9 1.8.7-.2 1.5c-3.3.2-6.2-2.7-6-6z" fill="var(--orange)"/></svg>
        <span>0171 204 3958</span>
      </li>
      <li class="contact-item">
        <svg class="contact-icon" viewBox="0 0 16 16"><circle cx="8" cy="8" r="8" fill="var(--ink)"/><rect x="4" y="5.2" width="8" height="5.6" rx="0.8" fill="none" stroke="var(--orange)" stroke-width="1"/><path d="M4.3 5.6L8 8.4l3.7-2.8" fill="none" stroke="var(--orange)" stroke-width="1"/></svg>
        <span>info@lindqvar-staff.de</span>
      </li>
      <li class="contact-item address">
        <svg class="contact-icon" viewBox="0 0 16 16"><circle cx="8" cy="8" r="8" fill="var(--ink)"/><path d="M8 3.5a3 3 0 0 1 3 3c0 2.2-3 5.5-3 5.5S5 8.7 5 6.5a3 3 0 0 1 3-3z" fill="var(--orange)"/><circle cx="8" cy="6.5" r="1.1" fill="var(--ink)"/></svg>
        <span>Lindqvar Staff GmbH<br>Falkertstraße 27a<br>70176 Stuttgart</span>
      </li>
      <li class="contact-item">
        <svg class="contact-icon" viewBox="0 0 16 16"><circle cx="8" cy="8" r="8" fill="var(--ink)"/><g fill="none" stroke="var(--orange)" stroke-width="0.9"><circle cx="8" cy="8" r="4.5"/><ellipse cx="8" cy="8" rx="2" ry="4.5"/><path d="M3.5 8h9"/></g></svg>
        <span>lindqvar-staff.de</span>
      </li>
    </ul>
  </section>
</main>
</body>
</html>
```